High end Electrical/home automation Business Card

Need a card for a high end electrical and home automation company utilising the existing logo.
Phone
Email
Website

Like black look with raised detail. Don’t necessarily need to keep colour of logo it could be made grayscale or white etc

Target Market(s)

High end clients

Contact Information for Business Card

Brightmoor Electrical

Requirements
Must have
• Logo, phone, email, website, address

High end look
Nice to have
• Black background card
Raised font
Should not have
• Lots of colour

```html
<!DOCTYPE html>
<html lang="en">
<head>
<meta charset="utf-8">
<title>Brightmoor Electrical – Business Card</title>
<link rel="stylesheet" href="https://fonts.googleapis.com/css2?family=Roboto:wght@300;400;500;700&display=swap">
<style>
  :root {
    --backdrop: #e9e9ea;
    --card: #3f3f44;
    --card-edge: #1f8ddb;
    --accent: #1f8ddb;
    --text-light: #f2f2f2;
    --text-muted: #d6d6d8;
    --divider: #8a8a90;
    --emboss: #46464c;
    --emboss-edge: #35353a;
  }
  * { box-sizing: border-box; margin: 0; padding: 0; }
  html, body {
    width: 1200px;
    height: 801px;
    overflow: hidden;
    background: var(--backdrop);
    font-family: "Roboto", Arial, sans-serif;
  }
  .stage {
    width: 1200px;
    height: 801px;
    display: flex;
    align-items: center;
    justify-content: center;
    gap: 60px;
  }
  .card {
    position: relative;
    width: 525px;
    height: 300px;
    background: var(--card);
    border-bottom: 4px solid var(--card-edge);
    box-shadow: 0 6px 18px rgba(0,0,0,0.18);
    color: var(--text-light);
    overflow: hidden;
  }

  /* Front */
  .brand-block {
    position: absolute;
    left: 40px;
    top: 40px;
    width: 222px;
    display: flex;
    flex-direction: column;
    align-items: center;
    gap: 10px;
  }
  .brand-mark {
    width: 34px;
    height: 34px;
    border-radius: 50%;
    background: var(--accent);
  }
  .brand-name {
    font-size: 22px;
    font-weight: 700;
    letter-spacing: -0.3px;
    color: var(--text-light);
    white-space: nowrap;
  }
  .holder {
    position: absolute;
    left: 40px;
    top: 140px;
    width: 208px;
    text-align: right;
  }
  .holder-name {
    font-size: 22px;
    font-weight: 500;
    color: var(--accent);
    white-space: nowrap;
  }
  .holder-role {
    font-size: 15px;
    font-weight: 400;
    color: var(--text-muted);
    margin-top: 2px;
  }
  .divider {
    position: absolute;
    left: 264px;
    top: 124px;
    width: 1px;
    height: 82px;
    background: var(--divider);
  }
  .contact-list {
    position: absolute;
    left: 282px;
    top: 126px;
    list-style: none;
    font-size: 14px;
    font-weight: 300;
    color: var(--text-light);
  }
  .contact-list li {
    display: flex;
    align-items: center;
    gap: 9px;
    height: 26px;
    white-space: nowrap;
  }
  .contact-list svg { width: 12px; height: 12px; flex: none; }
  .web-accent { color: var(--accent); }
  .address {
    position: absolute;
    left: 40px;
    right: 40px;
    top: 236px;
    font-size: 15px;
    font-weight: 300;
    color: var(--text-light);
    text-align: center;
  }

  /* Back */
  .emboss-disc {
    position: absolute;
    left: 40px;
    top: 40px;
    width: 240px;
    height: 240px;
    border-radius: 50%;
    background: var(--emboss);
    box-shadow: inset -3px -3px 6px var(--emboss-edge), inset 3px 3px 6px rgba(255,255,255,0.05);
  }
  .back-name {
    position: absolute;
    right: 34px;
    bottom: 46px;
    font-size: 36px;
    font-weight: 700;
    letter-spacing: -0.5px;
    color: var(--text-light);
    white-space: nowrap;
  }
</style>
</head>
<body>
<main class="stage">
  <section class="card card-front" aria-label="Business card front">
    <div class="brand-block">
      <span class="brand-mark" aria-hidden="true"></span>
      <span class="brand-name">Brightmoor Electrical</span>
    </div>

    <div class="holder">
      <p class="holder-name">Daniel Whitford</p>
      <p class="holder-role">Manager</p>
    </div>

    <div class="divider"></div>

    <ul class="contact-list">
      <li>
        <svg viewBox="0 0 24 24" aria-hidden="true"><path fill="#1f8ddb" d="M6.6 10.8a15.1 15.1 0 0 0 6.6 6.6l2.2-2.2c.3-.3.7-.4 1-.2 1.1.4 2.3.6 3.6.6.6 0 1 .4 1 1V20c0 .6-.4 1-1 1A17 17 0 0 1 3 4c0-.6.4-1 1-1h3.5c.6 0 1 .4 1 1 0 1.3.2 2.5.6 3.6.1.3 0 .7-.2 1z"/></svg>
        555-014-2210
      </li>
      <li>
        <svg viewBox="0 0 24 24" aria-hidden="true"><rect x="3" y="5" width="18" height="14" fill="none" stroke="#1f8ddb" stroke-width="2"/><path d="M3 6l9 7 9-7" fill="none" stroke="#1f8ddb" stroke-width="2"/></svg>
        hello@brightmoormail.com
      </li>
      <li>
        <svg viewBox="0 0 24 24" aria-hidden="true"><circle cx="12" cy="12" r="9" fill="none" stroke="#1f8ddb" stroke-width="2"/><path d="M3 12h18M12 3c3 3 3 15 0 18M12 3c-3 3-3 15 0 18" fill="none" stroke="#1f8ddb" stroke-width="1.6"/></svg>
        <span>www.<span class="web-accent">yourwebsite</span>.com</span>
      </li>
    </ul>

    <p class="address">Your address, city, state, ZIP 0000</p>
  </section>

  <section class="card card-back" aria-label="Business card back">
    <span class="emboss-disc" aria-hidden="true"></span>
    <p class="back-name">Brightmoor Electrical</p>
  </section>
</main>
</body>
</html>
```